KVR Inc Web Design

WHAT ARE WE DOING?
We are developing a new website look and feel for a new company called KVR Inc. This new look and feel should include colors, design elements, choice of photography and other imagery, fonts, and other user experience elements.

WHAT DO THEY DO?
KVR, Inc, makes tools for researchers who are studying protein-protein interactions. These molecules are the basic tools of biology, and serve as key targets for drug developers and disease researchers. The world of proteins is enormously complex, and companies like KVR provide researchers with critical tools that help them elucidate this world.

WHO ARE WE TALKING TO?
The target audience for this website are professional scientists working in university research or biopharma drug development. They are highly sophisticated consumers looking for key tools that will advance their research.

WHAT DO WE WANT THEM TO DO?
The site is an information resource for the customer exploring the tools that KVR sells and the scientific issues surrounding protein-protein interactions. They should be able to navigate easily to their content of choice, while the whole site should convey a professionalism that enhanced KVR’s credibility.

WHAT DOES THE KVR BRAND STAND FOR?
KVR stands for illumination. Proteins are challenging to study, and KVR exists to help shed light on their workings.

WHAT ARE THE KEY VALUES OF THE KVR BRAND?
Integrity. Innovation. Insight.

WHAT ARE THE EXECUTIONAL MANDITORIES?
The look and feel is completely up for grabs. Nothing is off the table.

WHAT ARE THE DELIVERABLES?
We need new designs for the following templates:
http://cms.marlowbench.com/
http://cms.marlowbench.com/products-and-services/instruments-3/bench-top-instruments/
http://cms.marlowbench.com/category/lab-study/

```html
<!DOCTYPE html>
<html lang="en">
<head>
<meta charset="utf-8">
<title>KVR Inc — Learning Center</title>
<link rel="stylesheet" href="https://fonts.googleapis.com/css2?family=Montserrat:wght@300;400;500;600&display=swap">
<style>
:root{
  --orange:#f9b54a;
  --orange-light:#fbc46a;
  --accent:#f7a52c;
  --brown:#5f4a31;
  --field:#a8988a;
  --teal:#35a9d6;
  --text:#3f3f3f;
  --muted:#6a6a6a;
  --rule:#d6d6d6;
  --white:#ffffff;
}
*{box-sizing:border-box;margin:0;padding:0}
html,body{width:1127px;height:1200px;overflow:hidden;background:var(--white)}
body{font-family:"Montserrat",sans-serif;color:var(--text)}
.page{position:absolute;left:0;top:0;width:1400px;height:1490px;transform:scale(0.805);transform-origin:0 0}
.abs{position:absolute}
a{text-decoration:none;color:inherit}

.topbar{left:0;top:0;width:1400px;height:77px;background:var(--orange)}
.brand{left:187px;top:17px;font-size:34px;font-weight:300;letter-spacing:9px;color:var(--white)}
.nav a{position:absolute;top:20px;height:32px;line-height:32px;color:var(--white);font-size:15px;font-weight:600;letter-spacing:-.3px;white-space:nowrap}
.nav a.active{background:var(--brown);border-radius:16px;text-align:center}
.site-search{left:1065px;top:23px;width:147px;height:26px;background:var(--orange-light);color:#8a6a3a;font-size:13px;padding:5px 8px;border:1px solid #e9a43c}
.site-search svg{position:absolute;right:6px;top:5px}

.featured-title{left:186px;top:128px;font-size:28px;font-weight:400;color:#1f1f1f}
.double-rule{left:187px;top:168px;width:1025px;height:5px;border-top:1px solid var(--rule);border-bottom:1px solid var(--rule)}
.featured-sub{left:187px;top:186px;font-size:21px;color:#1f1f1f;letter-spacing:-.2px}
.featured-sub a{color:var(--accent);font-size:18px;margin-left:20px}

.filter-band{left:187px;top:229px;width:1025px;height:62px;background:var(--brown)}
.field{top:18px;height:26px;background:var(--field);color:var(--white);font-size:14px;padding:4px 16px}
.field svg{position:absolute;right:14px;top:9px}
.search-btn{left:869px;top:18px;width:130px;height:26px;border-radius:13px;background:var(--accent);color:var(--white);font-size:14px;font-weight:600;text-align:center;line-height:26px;letter-spacing:-.2px}

.sidebar{left:187px;top:328px;width:237px;height:794px;border:1px solid var(--rule);box-shadow:0 1px 2px rgba(0,0,0,.15)}
.side-head{background:var(--brown);color:var(--white);font-size:18px;font-weight:500;padding:0 20px}
.side-list{list-style:none;margin-top:8px}
.side-list li{height:36px;line-height:36px;font-size:16px;color:#555;padding-left:20px;border-bottom:1px solid #e4e4e4}
.side-list li:last-child{border-bottom:none}
.side-list li::before{content:"›";font-size:14px;margin-right:8px}
.side-list li.active{background:var(--orange);color:var(--white)}
.promo-img{left:17px;top:434px;width:202px;height:202px;background:linear-gradient(150deg,#c9dcee,#7ea4cf 55%,#e9eef4)}
.promo-text{left:16px;top:648px;width:215px;font-size:13px;line-height:18px;color:#555;letter-spacing:-.3px}
.promo-btn{left:13px;top:716px;width:130px;height:27px;border-radius:14px;background:var(--accent);color:var(--white);font-size:14px;text-align:center;line-height:27px}

.order-bar{left:449px;top:328px;display:flex;align-items:center;font-size:13.5px}
.order-tag{background:#b5b5b5;color:var(--white);height:26px;line-height:26px;padding:0 16px;position:relative}
.order-tag::after{content:"";position:absolute;right:-10px;top:0;border-left:10px solid #b5b5b5;border-top:13px solid transparent;border-bottom:13px solid transparent}
.order-bar a{color:var(--accent);margin-left:12px}

.card{width:240px}
.thumb{width:237px;height:184px;border:1px solid var(--rule);padding:6px}
.thumb div{width:100%;height:100%}
.card h3{font-size:14.5px;font-weight:500;color:var(--teal);margin-top:13px;line-height:19px;letter-spacing:-.2px}
.card p{font-size:13px;color:#4a4a4a;line-height:18px;margin-top:3px;letter-spacing:-.2px}
.card p+p{margin-top:0}
.card .more{display:block;font-size:13px;color:var(--accent);margin-top:4px}
.card .more.dark{color:#111}

.foot-rule{left:187px;top:1337px;width:1025px;height:4px;border-top:1px solid var(--rule);border-bottom:1px solid var(--rule)}
.foot-mark{left:686px;top:1366px;width:29px;height:3px;background:var(--accent)}
.foot-links{left:0;top:1384px;width:1400px;text-align:center;font-size:13px;color:#444}
.foot-copy{left:0;top:1406px;width:1400px;text-align:center;font-size:13.5px;color:#444}
.social{left:664px;top:1431px;display:flex;gap:5px}
.social span{width:21px;height:21px;border-radius:50%;background:#555}
</style>
</head>
<body>
<div class="page">

  <header class="abs topbar">
    <div class="abs brand">KVRINC</div>
    <nav class="nav">
      <a style="left:386px">Company</a>
      <a class="active" style="left:470px;width:179px">Products &amp; Services</a>
      <a style="left:660px">Learning Center</a>
      <a style="left:800px">Events</a>
      <a style="left:876px">KVR News</a>
      <a style="left:973px">Contact</a>
    </nav>
    <div class="abs site-search">Search
      <svg width="14" height="14" viewBox="0 0 14 14"><circle cx="6" cy="6" r="4.5" fill="none" stroke="#c58e3e" stroke-width="1.6"/><line x1="9.3" y1="9.3" x2="13" y2="13" stroke="#c58e3e" stroke-width="1.8"/></svg>
    </div>
  </header>

  <h1 class="abs featured-title">FEATURED REPORT</h1>
  <div class="abs double-rule"></div>
  <div class="abs featured-sub">Screening assays for GPCR ligands 3 <a>Read &amp; Download ➜</a></div>

  <div class="abs filter-band">
    <div class="abs field" style="left:23px;width:277px">Keyword</div>
    <div class="abs field" style="left:311px;width:257px">Topic<svg width="14" height="8"><path d="M0 0h14L7 8z" fill="#fff"/></svg></div>
    <div class="abs field" style="left:580px;width:267px">Media Types<svg width="14" height="8"><path d="M0 0h14L7 8z" fill="#fff"/></svg></div>
    <div class="abs search-btn">⚲ Search Now</div>
  </div>

  <aside class="abs sidebar">
    <div class="side-head" style="height:43px;line-height:43px">Overview</div>
    <ul class="side-list">
      <li>Application Note</li><li class="active">Manual</li><li>PDF’s</li><li>Report</li><li>White Paper</li><li>Pipette Calibration</li><li>Application Note</li><li>Common Errors</li>
    </ul>
    <div class="abs side-head" style="left:0;top:357px;width:235px;height:63px;padding-top:11px;line-height:20px">Ready to save time<br>in your lab?</div>
    <div class="abs promo-img" role="img" aria-label="Automated lab instrument with pipetting head over sample plates"></div>
    <p class="abs promo-text">to have a member of our team<br>Demo what KVR’s instruments<br>could do for you.</p>
    <div class="abs promo-btn">Click Here</div>
  </aside>

  <div class="abs order-bar">
    <span class="order-tag">Order by</span>
    <a style="margin-left:22px">DATE</a><span style="color:var(--accent);margin-left:10px">|</span><a style="margin-left:8px">TITLE</a>
    <a style="margin-left:16px">ASCENDING ▾</a><a style="margin-left:26px">DESCENDING ▴</a>
  </div>

  <article class="abs card" style="left:450px;top:376px">
    <div class="thumb"><div role="img" aria-label="Lab scientist at a microscope" style="background:linear-gradient(120deg,#dfe7ef,#7ea6d0 60%,#e9edf1)"></div></div>
    <h3>Sample Prep Checklist</h3><p>Dr. Helen Marsh, Aug 2013</p><p>Application Note, Manual</p><a class="more">Read More ➜</a>
  </article>
  <article class="abs card" style="left:713px;top:376px">
    <div class="thumb"><div role="img" aria-label="Researchers working in a lab" style="background:linear-gradient(120deg,#d6e3ee,#f0ece6 55%,#9ab6d4)"></div></div>
    <h3>Screening Assays for GPCR...</h3><p>Dr. Owen Pryce, Aug 2013</p><p>Application Note, Video</p><a class="more">Read More ➜</a>
  </article>
  <article class="abs card" style="left:976px;top:376px">
    <div class="thumb"><div role="img" aria-label="Multichannel pipette tips over a well plate" style="background:linear-gradient(180deg,#2e6fb8,#4fb0e6 55%,#9fd7f2)"></div></div>
    <h3>Lorem ipsum dolor sit amet,<br>consectetur adipiscing elit</h3><p>Northfield University, July 2013</p><p>Manual, Report</p><a class="more dark">Read More ➜</a>
  </article>

  <article class="abs card" style="left:450px;top:694px">
    <div class="thumb"><div role="img" aria-label="Grey lab mouse on white" style="background:radial-gradient(circle at 50% 55%,#9a9a9a,#d8d8d8 40%,#ffffff 70%)"></div></div>
    <h3>Nam venenatis nisl libero</h3><p>Northfield University, July 2013</p><p>Manual, Report</p><a class="more">Read More ➜</a>
  </article>
  <article class="abs card" style="left:713px;top:694px">
    <div class="thumb"><div role="img" aria-label="Scientists handling plant samples" style="background:linear-gradient(120deg,#b9c9d9,#eef1f4 50%,#7f9dc2)"></div></div>
    <h3>Duis aliquam purus sed nulla<br>faucibus</h3><p>Lucas Ferrand PHD</p><a class="more">Read More ➜</a>
  </article>
  <article class="abs card" style="left:976px;top:694px">
    <div class="thumb"><div role="img" aria-label="Scientists handling plant samples" style="background:linear-gradient(120deg,#b9c9d9,#eef1f4 50%,#7f9dc2)"></div></div>
    <h3>Sample Prep Checklist</h3><p>Dr. Helen Marsh, Aug 2013</p><p>Application Note, Manual</p><a class="more">Read More ➜</a>
  </article>

  <article class="abs card" style="left:450px;top:1015px">
    <div class="thumb"><div role="img" aria-label="Lab scientist at a microscope" style="background:linear-gradient(120deg,#dfe7ef,#7ea6d0 60%,#e9edf1)"></div></div>
    <h3>Lorem ipsum dolor sit amet nisl<br>consectetur adipiscing elit</h3><p>Dr. Helen Marsh, Aug 2013</p><p>&nbsp;PDF, White Paper</p><a class="more">Read More ➜</a>
  </article>
  <article class="abs card" style="left:713px;top:1015px">
    <div class="thumb"><div role="img" aria-label="Researchers working in a lab" style="background:linear-gradient(120deg,#d6e3ee,#f0ece6 55%,#9ab6d4)"></div></div>
    <h3>Screening Assays for GPCR...</h3><p>Dr. Helen Marsh, Aug 2013</p><p>Application Note, Manual</p><a class="more">Read More ➜</a>
  </article>
  <article class="abs card" style="left:976px;top:1015px">
    <div class="thumb"><div role="img" aria-label="Team of scientists in safety glasses" style="background:linear-gradient(120deg,#8a7668,#e8e4df 45%,#c4ccd6)"></div></div>
    <h3>Nam venenatis nisl libero</h3><p>Dr. Helen Marsh, Aug 2013</p><p>Application Note, Manual</p><a class="more">Read More ➜</a>
  </article>

  <footer>
    <div class="abs foot-rule"></div>
    <div class="abs foot-mark"></div>
    <div class="abs foot-links">Company &nbsp;-&nbsp; Products &amp; Services &nbsp;-&nbsp; Learning Center &nbsp;-&nbsp; Events &nbsp;-&nbsp; KVR News &nbsp;-&nbsp; Contact</div>
    <div class="abs foot-copy">Copyright © KVR Inc. 2013</div>
    <div class="abs social"><span></span><span></span><span></span></div>
  </footer>

</div>
</body>
</html>
```